Personal Chef Needs a Good Web Design

Hi everyone!
My name is Leo, I work as a private chef for last 10 years, traveling all around the world and cooking in private megayacht and villas.
I'm about to settle down in my hometown in Europe for a while. And therefore I need a website that will show my story, pics and recipes, nutritional advices and of course offer a Personal and Private Chef services( working for 4-5 families and bringing delicious food to their house).
My clients are extremely rich folks, but usually are down to earth ones.
I believe, the web site should be focused on attention to:
-VIP person's wife( as she is usually responsible for food for family) and be simple.
-to famous people agents and be on high level.

There will be about 10 different menus and 6 different service offers

--UPDATE--
Logo Design:
+My thoughts are- printed structure of the vegetable or fruit on a white font. Like you slice the buffalo tomato, put it in red paint and print it on the edge of the page. See attached files named logo. Can be any nice structured thing, like tomato, lemon, red cabbage etc.
+Classic logos with chef's hat or knives are good too.
+Need to have the space for me to add the name( the fonts can be provided)

Target Market(s)

Private person. 80% Russian clients.

Industry/Entity Type

Cooking

Coding

Coded - Design and coding required

Number of Pages Required

3 page

Requirements
Must have
• Contact form/ Request back call/ Schedule a free consultation
Nice to have
• The client will need to choose straight ahead from the range of services I offer, like:
• -Private Chef( cooking only for the client)
• -Personal Chef( cooking for around 5 clients, bringing the ready to be heated food to their door)
• -Romantic dinner for two
• -Professional Sommelier service
• -Build your kitchen( offering design, equipment and that will fit your requirements)
• -Other( flowers, waiters, barista, equipment rental)
• So this column should go right after the introduction/aboutme part and will lead to separate pages with how-it-works thing for each.

```html
<!DOCTYPE html>
<html lang="en">
<head>
<meta charset="utf-8">
<title>Leo Chef — Private Chef</title>
<link rel="stylesheet" href="https://fonts.googleapis.com/css2?family=Montserrat:wght@400;500;600;700&family=Open+Sans:wght@400;600;700&display=swap">
<style>
:root{
  --accent:#d4934a;
  --ink:#1c1c1c;
  --text:#555;
  --muted:#888;
  --line:#d9d9d9;
  --white:#fff;
  --hero-a:#3a2a22;
  --hero-b:#6b4a36;
}
*{box-sizing:border-box;margin:0;padding:0}
html,body{width:1200px;height:2932px;overflow:hidden}
body{position:relative;background:var(--white);font-family:"Open Sans",Arial,sans-serif;color:var(--text)}
.heading{font-family:"Montserrat",Arial,sans-serif;color:var(--ink)}

/* Hero */
.hero{position:absolute;left:0;top:0;width:1200px;height:558px;
  background:radial-gradient(ellipse at 50% 45%,#7a5640 0%,#4a3328 45%,#2a1f1a 100%)}
.hero-photo{position:absolute;inset:0;background:linear-gradient(120deg,rgba(60,90,40,.35),transparent 35%,transparent 70%,rgba(70,100,40,.35))}
.site-name{position:absolute;left:98px;top:32px;font-family:"Montserrat",sans-serif;font-weight:600;font-size:22px;color:var(--white);letter-spacing:.5px}
.menu-button{position:absolute;left:1064px;top:28px;width:36px;height:36px;border:2px solid var(--white);border-radius:50%}
.menu-button span{position:absolute;left:10px;width:12px;height:2px;background:var(--white)}
.hero-brand{position:absolute;left:0;top:0;width:1200px;text-align:center;color:var(--white)}
.hero-years{position:absolute;top:150px;width:100%;font-size:15px;letter-spacing:7px;text-transform:uppercase}
.hero-logo{position:absolute;top:218px;width:100%;font-family:"Montserrat",sans-serif;font-weight:400;font-size:62px;letter-spacing:2px;display:flex;justify-content:center;align-items:center;gap:22px}
.hero-logo i{width:18px;height:18px;border-radius:50%;background:var(--white);display:block}
.hero-rule{position:absolute;top:326px;left:532px;width:136px;height:3px;background:var(--white)}
.hero-tagline{position:absolute;top:346px;width:100%;font-family:"Montserrat",sans-serif;font-weight:600;font-size:31px}
.hero-dots{position:absolute;top:497px;left:550px;display:flex;gap:8px}
.hero-dots span{width:14px;height:14px;border:2px solid var(--white);border-radius:50%}
.hero-dots span.active{background:var(--accent);border-color:var(--accent)}

/* Recipes */
.section-title{position:absolute;left:0;width:1200px;text-align:center;font-family:"Montserrat",sans-serif;font-weight:600;font-size:31px;color:var(--ink)}
.recipes{position:absolute;left:98px;top:700px;display:grid;grid-template-columns:490px 490px;column-gap:22px;row-gap:22px}
.recipe-card{height:196px;display:flex;border:1px solid var(--line);box-shadow:0 1px 3px rgba(0,0,0,.12);background:var(--white)}
.recipe-photo{width:188px;height:100%;flex:none}
.recipe-body{padding:14px 18px 0 20px}
.recipe-title{font-family:"Montserrat",sans-serif;font-weight:500;font-size:19px;color:var(--ink);text-transform:uppercase;margin-bottom:10px}
.recipe-list{list-style:none}
.recipe-list li{font-size:11px;line-height:25px;color:#333;display:flex;align-items:center;gap:8px;white-space:nowrap}
.recipe-list svg{flex:none}
.recipe-more{display:block;margin-top:8px;font-size:10.5px;font-weight:700;color:var(--accent)}
.recipe-card.featured{background:var(--accent);border-color:var(--accent)}
.recipe-card.featured .recipe-title,.recipe-card.featured li,.recipe-card.featured .recipe-more{color:var(--white)}
.p1{background:linear-gradient(135deg,#d8c9b2,#b98a55)}
.p2{background:linear-gradient(135deg,#5a2b24,#9a4a3e)}
.p3{background:linear-gradient(135deg,#6a3418,#b8642a)}
.p4{background:linear-gradient(135deg,#3b2a1c,#a4622f)}
.p5{background:linear-gradient(135deg,#d99a6a,#c2552f)}
.p6{background:linear-gradient(135deg,#2c2620,#5a3a28)}
.p7{background:linear-gradient(135deg,#c8b690,#7f7a45)}
.p8{background:linear-gradient(135deg,#4a2c1c,#8d5a32)}
.p9{background:linear-gradient(135deg,#a6592e,#d59a55)}
.p10{background:linear-gradient(135deg,#3a2018,#b04a2a)}

/* About */
.about-photo{position:absolute;left:98px;top:1884px;width:345px;height:406px;border:5px solid #e6e6e6;background:linear-gradient(160deg,#6d6a64,#a99a86 55%,#e8e4de)}
.about-title{position:absolute;left:502px;top:1884px;font-family:"Montserrat",sans-serif;font-weight:600;font-size:28px;color:var(--ink)}
.about-text{position:absolute;left:502px;top:1944px;width:598px;font-size:11.5px;line-height:29px;color:#666}
.about-text p+p{margin-top:28px}
.button{display:inline-block;background:var(--accent);color:var(--white);font-size:11px;font-weight:700;text-transform:uppercase}
.about-more{position:absolute;left:502px;top:2252px;width:120px;height:35px;line-height:35px;text-align:center}

.divider{position:absolute;left:0;top:2369px;width:1200px;height:5px;background:var(--accent)}

/* Contact */
.label-heading{font-family:"Montserrat",sans-serif;font-weight:600;font-size:14px;color:var(--ink);text-transform:uppercase}
.contact-form{position:absolute;left:98px;top:2492px;width:632px}
.field-label{display:block;font-size:10.5px;color:#555;text-transform:uppercase}
.field{border:1px solid #bdbdbd;background:var(--white)}
.contact-info{position:absolute;left:809px;top:2492px;width:300px}
.info-row{display:flex;align-items:center;gap:22px;font-size:11.5px;line-height:21px;color:#555}
.info-row .icon{width:36px;height:36px;border:1.5px solid var(--accent);border-radius:50%;display:flex;align-items:center;justify-content:center;flex:none}
.hours{width:100%;border-collapse:collapse;font-size:11.5px;color:#555}
.hours td{padding:6px 0}

/* Footer */
.footer-rule{position:absolute;left:98px;top:2858px;width:1002px;height:1px;background:var(--line)}
.copyright{position:absolute;left:98px;top:2886px;font-size:11.5px;color:#666}
.social{position:absolute;left:954px;top:2880px;display:flex;gap:12px}
.social span{width:26px;height:26px;background:#8e8e8e;border-radius:3px}
</style>
</head>
<body>

<header class="hero">
  <div class="hero-photo" role="img" aria-label="Close-up photograph of a grilled steak dish with herbs and cherry tomatoes"></div>
  <div class="site-name">LEO CHEF</div>
  <div class="menu-button" aria-label="Menu"><span style="top:11px"></span><span style="top:16px"></span><span style="top:21px"></span></div>
  <div class="hero-brand">
    <div class="hero-years">10 Years Experiences</div>
    <div class="hero-logo">LEO <i></i> CHEF</div>
    <div class="hero-rule"></div>
    <div class="hero-tagline">Private Chef in Megayacht and Villas</div>
  </div>
  <div class="hero-dots"><span class="active"></span><span></span><span></span><span></span><span></span></div>
</header>

<h2 class="section-title" style="top:622px">MY RECIPES</h2>

<section class="recipes">
  <article class="recipe-card featured">
    <div class="recipe-photo p1" role="img" aria-label="Fish tacos with lime and fresh herbs"></div>
    <div class="recipe-body">
      <h3 class="recipe-title">Seafood</h3>
      <ul class="recipe-list">
        <li><svg width="10" height="8" viewBox="0 0 10 8"><path d="M1 4l3 3 5-6" fill="none" stroke="#fff" stroke-width="2"/></svg>Thai Style Mahi with a Coconut Couscous</li>
        <li><svg width="10" height="8" viewBox="0 0 10 8"><path d="M1 4l3 3 5-6" fill="none" stroke="#fff" stroke-width="2"/></svg>Garlic and Herb Crusted Seabass</li>
        <li><svg width="10" height="8" viewBox="0 0 10 8"><path d="M1 4l3 3 5-6" fill="none" stroke="#fff" stroke-width="2"/></svg>Poached Halibut with Leeks &amp; Grape Tomatoes</li>
        <li><svg width="10" height="8" viewBox="0 0 10 8"><path d="M1 4l3 3 5-6" fill="none" stroke="#fff" stroke-width="2"/></svg>Miso Salmon with a Ginger Jasmine Rice</li>
      </ul>
      <span class="recipe-more">VIEW MORE &gt;&gt;</span>
    </div>
  </article>
  <article class="recipe-card">
    <div class="recipe-photo p2" role="img" aria-label="Sliced medium-rare beef steak"></div>
    <div class="recipe-body">
      <h3 class="recipe-title">Beef</h3>
      <ul class="recipe-list">
        <li><svg width="10" height="8" viewBox="0 0 10 8"><path d="M1 4l3 3 5-6" fill="none" stroke="#d4934a" stroke-width="2"/></svg>Grilled Teriyaki Steak Tips</li>
        <li><svg width="10" height="8" viewBox="0 0 10 8"><path d="M1 4l3 3 5-6" fill="none" stroke="#d4934a" stroke-width="2"/></svg>Slow Cooked Smokey Chipotle Tacos</li>
        <li><svg width="10" height="8" viewBox="0 0 10 8"><path d="M1 4l3 3 5-6" fill="none" stroke="#d4934a" stroke-width="2"/></svg>Beef Tenderloin in a Mushroom Brandy Sauce</li>
        <li><svg width="10" height="8" viewBox="0 0 10 8"><path d="M1 4l3 3 5-6" fill="none" stroke="#d4934a" stroke-width="2"/></svg>Penne Bolognese or Classic Meat Lasagna</li>
      </ul>
      <span class="recipe-more">VIEW MORE &gt;&gt;</span>
    </div>
  </article>
  <article class="recipe-card">
    <div class="recipe-photo p3" role="img" aria-label="Glazed roasted chicken wings"></div>
    <div class="recipe-body">
      <h3 class="recipe-title">Chicken</h3>
      <ul class="recipe-list">
        <li><svg width="10" height="8" viewBox="0 0 10 8"><path d="M1 4l3 3 5-6" fill="none" stroke="#d4934a" stroke-width="2"/></svg>Chicken with Arugula with a Basil Pasta Salad</li>
        <li><svg width="10" height="8" viewBox="0 0 10 8"><path d="M1 4l3 3 5-6" fill="none" stroke="#d4934a" stroke-width="2"/></svg>Baked Chicken with Sweet Potato and Radish</li>
        <li><svg width="10" height="8" viewBox="0 0 10 8"><path d="M1 4l3 3 5-6" fill="none" stroke="#d4934a" stroke-width="2"/></svg>Marsala, Mushrooms, Pancetta, Marsala wine</li>
        <li><svg width="10" height="8" viewBox="0 0 10 8"><path d="M1 4l3 3 5-6" fill="none" stroke="#d4934a" stroke-width="2"/></svg>Curry Spiced Chicken Breast with a Yogurt</li>
      </ul>
      <span class="recipe-more">VIEW MORE &gt;&gt;</span>
    </div>
  </article>
  <article class="recipe-card">
    <div class="recipe-photo p4" role="img" aria-label="Roasted pork joint with vegetables"></div>
    <div class="recipe-body">
      <h3 class="recipe-title">Pork</h3>
      <ul class="recipe-list">
        <li><svg width="10" height="8" viewBox="0 0 10 8"><path d="M1 4l3 3 5-6" fill="none" stroke="#d4934a" stroke-width="2"/></svg>Oriental Sweet and Sour Pork</li>
        <li><svg width="10" height="8" viewBox="0 0 10 8"><path d="M1 4l3 3 5-6" fill="none" stroke="#d4934a" stroke-width="2"/></svg>Maple Dijon Glazed Pork Medallions</li>
        <li><svg width="10" height="8" viewBox="0 0 10 8"><path d="M1 4l3 3 5-6" fill="none" stroke="#d4934a" stroke-width="2"/></svg>Crispy Corn Flake Pan Fried Pork Chops</li>
        <li><svg width="10" height="8" viewBox="0 0 10 8"><path d="M1 4l3 3 5-6" fill="none" stroke="#d4934a" stroke-width="2"/></svg>Creamy Pork Chops with Mushrooms, Hericot</li>
      </ul>
      <span class="recipe-more">VIEW MORE &gt;&gt;</span>
    </div>
  </article>
  <article class="recipe-card">
    <div class="recipe-photo p5" role="img" aria-label="Fried breaded shrimp"></div>
    <div class="recipe-body">
      <h3 class="recipe-title">Seafood</h3>
      <ul class="recipe-list">
        <li><svg width="10" height="8" viewBox="0 0 10 8"><path d="M1 4l3 3 5-6" fill="none" stroke="#d4934a" stroke-width="2"/></svg>Chicken with Arugula with a Basil Pasta Salad</li>
        <li><svg width="10" height="8" viewBox="0 0 10 8"><path d="M1 4l3 3 5-6" fill="none" stroke="#d4934a" stroke-width="2"/></svg>Baked Chicken with Sweet Potato and Radish</li>
        <li><svg width="10" height="8" viewBox="0 0 10 8"><path d="M1 4l3 3 5-6" fill="none" stroke="#d4934a" stroke-width="2"/></svg>Marsala, Mushrooms, Pancetta, Marsala wine</li>
        <li><svg width="10" height="8" viewBox="0 0 10 8"><path d="M1 4l3 3 5-6" fill="none" stroke="#d4934a" stroke-width="2"/></svg>Curry Spiced Chicken Breast with a Yogurt</li>
      </ul>
      <span class="recipe-more">VIEW MORE &gt;&gt;</span>
    </div>
  </article>
  <article class="recipe-card">
    <div class="recipe-photo p6" role="img" aria-label="Beef stew in a white bowl"></div>
    <div class="recipe-body">
      <h3 class="recipe-title">Beef</h3>
      <ul class="recipe-list">
        <li><svg width="10" height="8" viewBox="0 0 10 8"><path d="M1 4l3 3 5-6" fill="none" stroke="#d4934a" stroke-width="2"/></svg>Oriental Sweet and Sour Pork</li>
        <li><svg width="10" height="8" viewBox="0 0 10 8"><path d="M1 4l3 3 5-6" fill="none" stroke="#d4934a" stroke-width="2"/></svg>Maple Dijon Glazed Pork Medallions</li>
        <li><svg width="10" height="8" viewBox="0 0 10 8"><path d="M1 4l3 3 5-6" fill="none" stroke="#d4934a" stroke-width="2"/></svg>Crispy Corn Flake Pan Fried Pork Chops</li>
        <li><svg width="10" height="8" viewBox="0 0 10 8"><path d="M1 4l3 3 5-6" fill="none" stroke="#d4934a" stroke-width="2"/></svg>Creamy Pork Chops with Mushrooms, Hericot</li>
      </ul>
      <span class="recipe-more">VIEW MORE &gt;&gt;</span>
    </div>
  </article>
  <article class="recipe-card">
    <div class="recipe-photo p7" role="img" aria-label="Chicken with sautéed mushrooms"></div>
    <div class="recipe-body">
      <h3 class="recipe-title">Chicken</h3>
      <ul class="recipe-list">
        <li><svg width="10" height="8" viewBox="0 0 10 8"><path d="M1 4l3 3 5-6" fill="none" stroke="#d4934a" stroke-width="2"/></svg>Chicken with Arugula with a Basil Pasta Salad</li>
        <li><svg width="10" height="8" viewBox="0 0 10 8"><path d="M1 4l3 3 5-6" fill="none" stroke="#d4934a" stroke-width="2"/></svg>Baked Chicken with Sweet Potato and Radish</li>
        <li><svg width="10" height="8" viewBox="0 0 10 8"><path d="M1 4l3 3 5-6" fill="none" stroke="#d4934a" stroke-width="2"/></svg>Marsala, Mushrooms, Pancetta, Marsala wine</li>
        <li><svg width="10" height="8" viewBox="0 0 10 8"><path d="M1 4l3 3 5-6" fill="none" stroke="#d4934a" stroke-width="2"/></svg>Curry Spiced Chicken Breast with a Yogurt</li>
      </ul>
      <span class="recipe-more">VIEW MORE &gt;&gt;</span>
    </div>
  </article>
  <article class="recipe-card">
    <div class="recipe-photo p8" role="img" aria-label="Pork chop with creamy sauce"></div>
    <div class="recipe-body">
      <h3 class="recipe-title">Pork</h3>
      <ul class="recipe-list">
        <li><svg width="10" height="8" viewBox="0 0 10 8"><path d="M1 4l3 3 5-6" fill="none" stroke="#d4934a" stroke-width="2"/></svg>Oriental Sweet and Sour Pork</li>
        <li><svg width="10" height="8" viewBox="0 0 10 8"><path d="M1 4l3 3 5-6" fill="none" stroke="#d4934a" stroke-width="2"/></svg>Maple Dijon Glazed Pork Medallions</li>
        <li><svg width="10" height="8" viewBox="0 0 10 8"><path d="M1 4l3 3 5-6" fill="none" stroke="#d4934a" stroke-width="2"/></svg>Crispy Corn Flake Pan Fried Pork Chops</li>
        <li><svg width="10" height="8" viewBox="0 0 10 8"><path d="M1 4l3 3 5-6" fill="none" stroke="#d4934a" stroke-width="2"/></svg>Creamy Pork Chops with Mushrooms, Hericot</li>
      </ul>
      <span class="recipe-more">VIEW MORE &gt;&gt;</span>
    </div>
  </article>
  <article class="recipe-card">
    <div class="recipe-photo p9" role="img" aria-label="Baked salmon with lemon slices"></div>
    <div class="recipe-body">
      <h3 class="recipe-title">Seafood</h3>
      <ul class="recipe-list">
        <li><svg width="10" height="8" viewBox="0 0 10 8"><path d="M1 4l3 3 5-6" fill="none" stroke="#d4934a" stroke-width="2"/></svg>Chicken with Arugula with a Basil Pasta Salad</li>
        <li><svg width="10" height="8" viewBox="0 0 10 8"><path d="M1 4l3 3 5-6" fill="none" stroke="#d4934a" stroke-width="2"/></svg>Baked Chicken with Sweet Potato and Radish</li>
        <li><svg width="10" height="8" viewBox="0 0 10 8"><path d="M1 4l3 3 5-6" fill="none" stroke="#d4934a" stroke-width="2"/></svg>Marsala, Mushrooms, Pancetta, Marsala wine</li>
        <li><svg width="10" height="8" viewBox="0 0 10 8"><path d="M1 4l3 3 5-6" fill="none" stroke="#d4934a" stroke-width="2"/></svg>Curry Spiced Chicken Breast with a Yogurt</li>
      </ul>
      <span class="recipe-more">VIEW MORE &gt;&gt;</span>
    </div>
  </article>
  <article class="recipe-card">
    <div class="recipe-photo p10" role="img" aria-label="Grilled steak with cherry tomatoes"></div>
    <div class="recipe-body">
      <h3 class="recipe-title">Beef</h3>
      <ul class="recipe-list">
        <li><svg width="10" height="8" viewBox="0 0 10 8"><path d="M1 4l3 3 5-6" fill="none" stroke="#d4934a" stroke-width="2"/></svg>Oriental Sweet and Sour Pork</li>
        <li><svg width="10" height="8" viewBox="0 0 10 8"><path d="M1 4l3 3 5-6" fill="none" stroke="#d4934a" stroke-width="2"/></svg>Maple Dijon Glazed Pork Medallions</li>
        <li><svg width="10" height="8" viewBox="0 0 10 8"><path d="M1 4l3 3 5-6" fill="none" stroke="#d4934a" stroke-width="2"/></svg>Crispy Corn Flake Pan Fried Pork Chops</li>
        <li><svg width="10" height="8" viewBox="0 0 10 8"><path d="M1 4l3 3 5-6" fill="none" stroke="#d4934a" stroke-width="2"/></svg>Creamy Pork Chops with Mushrooms, Hericot</li>
      </ul>
      <span class="recipe-more">VIEW MORE &gt;&gt;</span>
    </div>
  </article>
</section>

<section>
  <div class="about-photo" role="img" aria-label="Portrait of the chef in a white jacket standing in a bakery"></div>
  <h2 class="about-title">LEO CHEF</h2>
  <div class="about-text">
    <p>At vero eos et accusamus et iusto odio dignissimos ducimus qui blanditiis praesentium voluptatum deleniti at que corrupti quos dolores et quas molestias excepturi.</p>
    <p>Sint occaecati cupiditate non provident, similique sunt in culpa qui officia deserunt mollitia animi, id est lab orum et dolorum fuga. Et harum quidem rerum facilis est et expedita distinctio. Nam libero tempore, cum soluta nobis est eligendi optio cumque nihil impedit quo minus id quod maxime placeat facere possimus nis voluptas assumenda est, omnis dolor repellendus. Temporibus autem quibusdam et aut officiis debitis aut rerum necessitatibus saepe eveniet ut et voluptates. Et harum quidem rerum facilis est et expedita dist inctio. Nam libero tempore, cum eligendi optio cumque nihil impe.</p>
  </div>
  <span class="button about-more">READ MORE &gt;&gt;</span>
</section>

<div class="divider"></div>

<h2 class="section-title" style="top:2412px">CONTACT US</h2>

<form class="contact-form">
  <div class="label-heading">Contact Form</div>
  <span class="field-label" style="position:absolute;left:0;top:46px">Name :</span>
  <span class="field-label" style="position:absolute;left:320px;top:46px">Phone No :</span>
  <div class="field" style="position:absolute;left:2px;top:70px;width:310px;height:35px"></div>
  <div class="field" style="position:absolute;left:320px;top:70px;width:312px;height:35px"></div>
  <span class="field-label" style="position:absolute;left:0;top:113px">Email :</span>
  <div class="field" style="position:absolute;left:2px;top:136px;width:630px;height:34px"></div>
  <span class="field-label" style="position:absolute;left:0;top:178px">Message :</span>
  <div class="field" style="position:absolute;left:2px;top:203px;width:630px;height:80px"></div>
  <span class="button" style="position:absolute;left:543px;top:295px;width:89px;height:33px;line-height:33px;text-align:center">Submit</span>
</form>

<aside class="contact-info">
  <div class="label-heading">Contact Information</div>
  <div class="info-row" style="margin-top:26px">
    <span class="icon"><svg width="14" height="16" viewBox="0 0 14 16"><path d="M7 15s5-5 5-9a5 5 0 0 0-10 0c0 4 5 9 5 9z" fill="none" stroke="#d4934a" stroke-width="1.5"/><circle cx="7" cy="6" r="1.8" fill="#d4934a"/></svg></span>
    <span>Harbour Lane 27<br>Porto Alto 4410</span>
  </div>
  <div class="info-row" style="margin-top:22px">
    <span class="icon"><svg width="14" height="11" viewBox="0 0 14 11"><rect x="0.5" y="0.5" width="13" height="10" fill="#d4934a"/><path d="M1 1l6 5 6-5" fill="none" stroke="#fff" stroke-width="1.2"/></svg></span>
    <span>info@leochef.com</span>
  </div>
  <div class="info-row" style="margin-top:22px">
    <span class="icon"><svg width="14" height="14" viewBox="0 0 14 14"><path d="M3 1l2 3-1.5 1.5c.8 2 2.2 3.4 4 4L9 8l3 2-1 3C5.5 13 1 8.5 1 3z" fill="#d4934a"/></svg></span>
    <span>1 - 555 - 010 - 2040</span>
  </div>
  <div class="label-heading" style="margin-top:30px">Opening Hours</div>
  <table class="hours" style="margin-top:12px">
    <tr><td style="width:118px">Monday - Wednesday</td><td style="width:24px">:</td><td>10:00 am - 10:00 pm</td></tr>
    <tr><td>Thursday &amp; Friday</td><td>:</td><td>10:00 am - 10:00 pm</td></tr>
    <tr><td>Saturday &amp; Sunday</td><td>:</td><td>9:00 am - 11:00 pm</td></tr>
  </table>
</aside>

<footer>
  <div class="footer-rule"></div>
  <div class="copyright">Copyrights © 2016, Leo Chef . All Rights Reserved.</div>
  <div class="social" aria-label="Social links"><span></span><span></span><span></span><span></span></div>
</footer>

</body>
</html>
```